Corporate Design für junge Steuerberater
Zielgruppe
Wir sind eine junge Steuerberatungsgesellschaft (2 jünge Mütter). Unsere Kunden sind überwiegend kleine Unternehmer
Aufgabenstellung
Logo und Geschäftspapiere sollen leger, aber seriös wirken.
Wir benötigen ein Logo, Visitenkarten, Briefpapier bzw. Deckblätter für unsere Bilanzen, Steuererklärungen. Deckblätter und Briefpapier können auch gleich aussehen.
(Das Beispielbild ist natürlich nicht von unserem Unternehmen, würde uns vom Stil her gut gefallen....ist aber kein Muss)

```html
<!DOCTYPE html>
<html lang="de">
<head>
<meta charset="utf-8">
<title>KLT Steuerberatung – Deckblätter</title>
<link rel="stylesheet" href="https://fonts.googleapis.com/css2?family=Exo+2:wght@700;800&display=swap">
<style>
  :root {
    --page-bg: #e9e7e4;
    --cover-bg: #373f47;
    --cover-mark: #3f4850;
    --accent-green: #4cbd87;
    --logo-grey: #b8bbbe;
    --title-white: #ffffff;
    --cover-shadow: rgba(0, 0, 0, 0.35);
  }
  * { margin: 0; padding: 0; box-sizing: border-box; }
  html, body {
    width: 1200px;
    height: 1189px;
    overflow: hidden;
    background: var(--page-bg);
  }
  .stage {
    position: relative;
    width: 1200px;
    height: 1189px;
  }
  .cover {
    position: absolute;
    width: 543px;
    height: 769px;
    background: var(--cover-bg);
    overflow: hidden;
    box-shadow: 0 6px 18px var(--cover-shadow);
    font-family: "Exo 2", sans-serif;
  }
  .cover--balance { left: 88px; top: 112px; z-index: 2; }
  .cover--tax { left: 568px; top: 268px; z-index: 1; }
  .cover__stripe {
    position: absolute;
    left: 0;
    top: 216px;
    bottom: 0;
    width: 14px;
    background: var(--accent-green);
  }
  .cover__brand {
    position: absolute;
    top: 68px;
    left: 0;
    width: 100%;
    padding-left: 30px;
    text-align: center;
    font-weight: 800;
    font-size: 52px;
    letter-spacing: 2px;
    color: var(--logo-grey);
    line-height: 1;
  }
  .cover__title {
    position: absolute;
    top: 212px;
    left: 0;
    width: 100%;
    text-align: center;
    font-weight: 700;
    font-size: 27px;
    letter-spacing: 1px;
    color: var(--title-white);
    line-height: 1.2;
  }
  .cover__backdrop-name {
    position: absolute;
    left: 34px;
    bottom: -28px;
    font-weight: 800;
    font-size: 190px;
    letter-spacing: 14px;
    color: var(--cover-mark);
    line-height: 1;
    white-space: nowrap;
  }
</style>
</head>
<body>
  <main class="stage">
    <section class="cover cover--balance">
      <div class="cover__stripe"></div>
      <div class="cover__backdrop-name" aria-hidden="true">KLT</div>
      <div class="cover__brand">KLT</div>
      <h1 class="cover__title">BILANZEN</h1>
    </section>
    <section class="cover cover--tax">
      <div class="cover__stripe"></div>
      <div class="cover__backdrop-name" aria-hidden="true">KLT</div>
      <div class="cover__brand">KLT</div>
      <h1 class="cover__title">STEUERERKLÄRUNGEN</h1>
    </section>
  </main>
</body>
</html>
```